Fenwick Grading LTD - website for irrigation & Landscape Lighting & Buried service wire

Looking for a website to help promote my business with Irrigation (installation, service, etc) and buried service wire/drainage solutions.

Commercial/Residential

Landscape lighting.

I’ll get photos in the trucks and trailers to upload as well maybe the machine as well.

Target Market(s)

Homeowners who want green grass and beautiful gardens. Beautiful landscape lighting

Industry/Entity Type

Irrigation systems and landscape lighting and buried service wire to homes and offering Drainage soltions.

Coding

Coded - Design and coding required

Number of Pages Required

4 page

Colors
F0912C
F2A743
F7CA91
FBE8D2
FDF5EE

Requirements
Must have
• was hoping to link up my email on fenwickgrading@mailbox-example.net with the website if possible.
Nice to have
• Page for Irrigation, page for landscape lighting, page buried service wire & drainage soltions.

```html
<!DOCTYPE html>
<html lang="en">
<head>
<meta charset="utf-8">
<title>Irrigation | Fenwick Grading LTD</title>
<link href="https://fonts.googleapis.com/css2?family=Montserrat:wght@300;400;500;600;700&family=Roboto+Condensed:wght@700&display=swap" rel="stylesheet">
<style>
:root{
  --orange:#F0912C;
  --orange-2:#F2A743;
  --peach:#F7CA91;
  --cream:#FBE8D2;
  --ivory:#FDF5EE;
  --ink:#111111;
  --text:#4a4a4a;
  --white:#ffffff;
  --black:#000000;
}
*{margin:0;padding:0;box-sizing:border-box}
html,body{width:791px;height:1200px;overflow:hidden;background:var(--white)}
body{position:relative;font-family:"Montserrat",sans-serif;color:var(--text)}
.abs{position:absolute}

/* hero */
.hero{left:0;top:0;width:791px;height:292px;background:linear-gradient(160deg,#3c4a22 0%,#4d5e27 30%,#5b5a2a 55%,#3b3a25 80%,#2a2a1e 100%)}
.hero-shade{left:0;top:0;width:791px;height:292px;background:linear-gradient(90deg,rgba(0,0,0,.25),rgba(0,0,0,.05) 50%,rgba(0,0,0,.3))}
.hero-edge{left:0;top:0}
.brand{display:flex;align-items:center;gap:6px;font-weight:700;color:var(--white);font-size:12px;letter-spacing:.5px}
.brand-dot{width:12px;height:12px;border-radius:50%;background:var(--orange)}
.header-brand{left:93px;top:26px}
.nav{top:22px;left:269px;display:flex;gap:0;font-size:8.6px;color:var(--white)}
.nav a{color:inherit;text-decoration:none;position:absolute;white-space:nowrap}
.nav a.active{color:var(--orange);border-bottom:1px solid var(--orange);padding-bottom:1px}
.btn-contact{left:620px;top:16px;width:78px;height:23px;border-radius:12px;background:var(--orange);color:var(--white);font-size:7.6px;font-weight:600;letter-spacing:.4px;display:flex;align-items:center;justify-content:center}
.page-title{left:93px;top:122px;font-family:"Roboto Condensed",sans-serif;font-weight:700;font-size:24px;color:var(--white)}
.crumbs{left:93px;top:153px;font-size:8.6px;color:var(--white)}
.crumbs b{font-weight:700}

/* intro */
.section-title{left:0;width:791px;top:342px;text-align:center;font-family:"Roboto Condensed",sans-serif;font-weight:700;font-size:24px;color:var(--ink)}
.section-title span{color:var(--orange)}
.section-sub{left:0;width:791px;top:388px;text-align:center;font-size:8.6px;font-weight:500;color:var(--ink)}
.sub-band{left:195px;top:376px}
.photo{left:93px;top:424px}
.copy{left:422px;top:423px;width:280px;font-size:8.5px;line-height:14.9px;font-weight:300}
.copy p{margin-bottom:10px}
.copy .lead{color:var(--ink);font-weight:400}
.ticks{list-style:none;margin-top:2px}
.ticks li{position:relative;padding-left:8px;margin-bottom:5px}
.ticks li::before{content:"";position:absolute;left:0;top:5px;width:4px;height:4px;border-radius:50%;background:var(--orange)}
.body-copy{left:94px;top:697px;width:604px;font-size:8.5px;line-height:14.9px;font-weight:300}
.body-copy p{margin-bottom:10px}

/* footer */
.footer-shape{left:0;top:915px}
.footer-brand{left:0;width:791px;top:996px;justify-content:center;font-size:16px}
.footer-brand .brand-dot{width:16px;height:16px}
.fnav{left:0;top:1076px;width:791px;height:14px;font-size:8.6px;color:var(--white)}
.fnav a{position:absolute;color:inherit;text-decoration:none;white-space:nowrap}
.fnav a.active{color:var(--orange);font-weight:600}
.fnav a.strong{font-weight:600;font-size:7.8px;letter-spacing:.3px}
.contact{display:flex;align-items:center;gap:7px;color:var(--white);font-size:8.6px;line-height:14px}
.contact svg{flex:none}
.rule{left:93px;top:1158px;width:605px;height:1px;background:#333}
.copyright{left:93px;top:1173px;font-size:8.6px;color:var(--white)}
.socials{left:596px;top:1168px;display:flex;gap:4.5px}
.socials span{width:22px;height:22px;border-radius:50%;border:1px solid var(--orange)}
</style>
</head>
<body>

<div class="abs hero" role="img" aria-label="Evening garden with lawn, shrub bed, stone border and lit garden lamp posts"></div>
<div class="abs hero-shade"></div>
<svg class="abs hero-edge" width="791" height="300" viewBox="0 0 791 300">
  <polygon points="0,240 395,288 791,235 791,300 0,300" fill="#fff"/>
  <polyline points="0,240 395,287 791,235" fill="none" stroke="#F0912C" stroke-width="3"/>
</svg>

<div class="abs brand header-brand"><span class="brand-dot"></span>FENWICK GRADING LTD</div>

<nav class="abs nav">
  <a style="left:0;top:0">Home</a>
  <a class="active" style="left:56px;top:0">Irrigation</a>
  <a style="left:125px;top:0">Landscape Lighting</a>
  <a style="left:239px;top:0">Trenching&nbsp; Services</a>
</nav>
<div class="abs btn-contact">CONTACT US</div>

<h1 class="abs page-title">Irrigation</h1>
<div class="abs crumbs">Home » <b>Irrigation</b></div>

<svg class="abs sub-band" width="400" height="50" viewBox="0 0 400 50">
  <polygon points="0,0 400,0 360,50 40,50" fill="#f7f7f7"/>
</svg>
<h2 class="abs section-title">Irrigation <span>Systems</span></h2>
<div class="abs section-sub">Efficient and Effective Watering Solutions for Your Lawn and Garden</div>

<svg class="abs photo" width="290" height="260" viewBox="0 0 290 260" role="img" aria-label="Lawn sprinkler spraying water over green grass">
  <defs>
    <linearGradient id="grass" x1="0" y1="0" x2="0" y2="1">
      <stop offset="0" stop-color="#8fb35a"/>
      <stop offset=".45" stop-color="#5f9a2c"/>
      <stop offset="1" stop-color="#2f5d16"/>
    </linearGradient>
  </defs>
  <polyline points="0,9 144,257 287,9" fill="none" stroke="#F0912C" stroke-width=".8"/>
  <polygon points="0,0 287,0 143,250" fill="url(#grass)"/>
</svg>

<div class="abs copy">
  <p class="lead">Our irrigation systems are designed to provide your lawn and garden with the right amount of water, without wasting a single drop. With our expert installation and service, you can rest assured that your plants will receive the nourishment they need to thrive.</p>
  <p>Lorem Ipsum is simply dummy text of the printing and typesetting industry. Lorem Ipsum has been the industry's standard dummy text ever since the 1500s, when an unknown printer took a galley of type and scrambled it to make a type specimen book. It has survived not only five centuries, but also the leap into electronic typesetting, remaining essentially unchanged. It was popularised in the 1960s with the release of Letraset sheets containing Lorem Ipsum passages,</p>
  <ul class="ticks">
    <li>Lorem Ipsum has been the industry's standard dummy.</li>
    <li>It has survived not only five centuries.</li>
    <li>when an unknown printer took a galley of type and scrambled.</li>
  </ul>
</div>

<div class="abs body-copy">
  <p>It is a long established fact that a reader will be distracted by the readable content of a page when looking at its layout. The point of using Lorem Ipsum is that it has a more-or-less normal distribution of letters, as opposed to using 'Content here, content here', making it look like readable English. Many desktop publishing packages and web page editors now use Lorem Ipsum as their default model text, and a search for 'lorem ipsum' will uncover many web sites still in their infancy. Various versions have evolved over the years, sometimes by accident, sometimes on purpose (injected humour and the like).</p>
  <p>There are many variations of passages of Lorem Ipsum available, but the majority have suffered alteration in some form, by injected humour, or randomised words which don't look even slightly believable. If you are going to use a passage of Lorem Ipsum, you need to be sure there isn't anything embarrassing hidden in the middle of text. All the Lorem Ipsum generators on the Internet tend to repeat predefined chunks as necessary, making this the first true generator on the Internet. It uses a dictionary of over 200 Latin words, combined with a handful of model sentence structures, to generate Lorem Ipsum which looks reasonable. The generated Lorem Ipsum is therefore always free from repetition, injected humour, or non-characteristic words etc.</p>
</div>

<svg class="abs footer-shape" width="791" height="285" viewBox="0 0 791 285">
  <polygon points="0,55 395,6 791,60 791,285 0,285" fill="#000"/>
  <polyline points="0,54 395,5 791,59" fill="none" stroke="#F0912C" stroke-width="5"/>
</svg>

<div class="abs brand footer-brand"><span class="brand-dot"></span>FENWICK GRADING LTD</div>

<nav class="abs fnav">
  <a style="left:184px">Home</a>
  <a class="active" style="left:246px">Irrigation</a>
  <a style="left:322px">Landscape Lighting</a>
  <a style="left:443px">Trenching&nbsp; Services</a>
  <a class="strong" style="left:561px;top:1px">Contact Us</a>
</nav>

<div class="abs contact" style="left:136px;top:1114px">
  <svg width="24" height="24" viewBox="0 0 24 24"><circle cx="12" cy="12" r="11.3" fill="none" stroke="#F0912C" stroke-width="1"/><path d="M12 6.5a3.3 3.3 0 0 0-3.3 3.3c0 2.5 3.3 6.2 3.3 6.2s3.3-3.7 3.3-6.2A3.3 3.3 0 0 0 12 6.5zm0 4.6a1.3 1.3 0 1 1 0-2.6 1.3 1.3 0 0 1 0 2.6z" fill="#fff"/></svg>
  <div>123, Building Name, Street<br>City, State XY 123456</div>
</div>
<div class="abs contact" style="left:348px;top:1114px">
  <svg width="24" height="24" viewBox="0 0 24 24"><circle cx="12" cy="12" r="11.3" fill="none" stroke="#F0912C" stroke-width="1"/><path d="M9.2 7.2l1.6 2.2-.9 1.1c.6 1.3 1.5 2.2 2.8 2.8l1.1-.9 2.2 1.6-.8 1.6c-3.6-.2-6.6-3.2-6.8-6.8z" fill="#fff"/></svg>
  <div>Phone<br>123-456-7890</div>
</div>
<div class="abs contact" style="left:504px;top:1114px">
  <svg width="24" height="24" viewBox="0 0 24 24"><circle cx="12" cy="12" r="11.3" fill="none" stroke="#F0912C" stroke-width="1"/><rect x="7.5" y="8.5" width="9" height="7" rx="1" fill="#fff"/><polyline points="7.8,9 12,12.3 16.2,9" fill="none" stroke="#000" stroke-width=".9"/></svg>
  <div>E-Mail<br>info@fenwickgrading-example.net</div>
</div>

<div class="abs rule"></div>
<div class="abs copyright">© 2024 Fenwick Grading Ltd . All Rights Reserved.</div>
<div class="abs socials" aria-label="Social media links">
  <span></span><span></span><span></span><span></span>
</div>

</body>
</html>
```